Business Card Design - Photographer

I am a landscape photographer and I require a business card design. 

I require two designs:
1)  a double sided business card
 and
b)  a single sided business card 

The single sided design can either be the same as the double sided (with just one side having all the information)....or it can be an entire new design. Its up to you.

My corporate colours are (CMYK):

Blue   69, 32, 0, 0
Grey  72,  64,  47,  31
Green  32,  2,  91,  0
Yellow   0, 19, 92, 0
Orange  0, 39, 75, 0

Colour space in final file should be in CMYK.

The details that need to be included on the card:

- Use the provided Logo
- Name: Wiktor Baranowski
- Email:   sales@vistalumeworks.com.au
- Website:    vistalumeworks.com.au
- Twitter:    twitter.com/vistalumeworks
- Facebook:   facebook.com/vistalumeworks
- Mobile  0417 539 662

Please use the attached template to design the logo to the specified size, including the marked bleed lines. I have also attached my logo in PNG (transparent background) and ai format for you to use.

The final file should be:
- Photoshop version with layers so I can edit the name/text etc. All non vector files should be high resolution at 1039 x 697 pixels at 300 dpi.

I also require a file as:
- Vector based PDF

Anyway questions please contact me.

Thank you

Industry/Entity Type

Landscape

Logo styles of interest
Pictorial/Combination Logo
Abstract Logo
Wordmark Logo
Lettermark Logo
Requirements
Must have
• The details that need to be included on the card:

- Use the provided Logo
- Name: Wiktor Baranowski
- Email: sales@vistalumeworks.com.au
- Website: vistalumeworks.com.au
- Twitter: twitter.com/vistalumeworks
- Facebook: facebook.com/vistalumeworks
- Mobile 0417 539 662

```html
<!DOCTYPE html>
<html lang="en">
<head>
<meta charset="utf-8">
<title>Vistalume Works – Business Cards</title>
<link rel="stylesheet" href="https://fonts.googleapis.com/css2?family=Open+Sans:wght@400;700&family=Cinzel:wght@500&display=swap">
<style>
  :root {
    --stage: #2e3533;
    --card: #ffffff;
    --navy: #3e4053;
    --orange: #f6a64a;
    --white: #ffffff;
    --sans: "Open Sans", Arial, sans-serif;
    --serif: "Cinzel", Georgia, serif;
  }
  * { box-sizing: border-box; margin: 0; padding: 0; }
  html, body {
    width: 987px; height: 1200px; overflow: hidden;
    background: var(--stage);
  }
  .canvas { position: relative; width: 987px; height: 1200px; }

  .card {
    position: absolute;
    width: 790px; height: 450px;
    background: var(--card);
    border-radius: 28px;
    overflow: hidden;
  }
  .card--front { left: 88px; top: 102px; }
  .card--back  { left: 91px; top: 637px; }

  .card__band { position: absolute; inset: 0; }

  .mark {
    position: absolute;
    border-radius: 50%;
    background: var(--navy);
  }
  .card--front .mark { left: 167px; top: 95px; width: 120px; height: 120px; }
  .card--front .brand-name {
    position: absolute; left: 60px; top: 250px; width: 334px;
    text-align: center;
    font-family: var(--serif); font-weight: 500; font-size: 28px;
    color: var(--navy); letter-spacing: 1px;
  }

  .holder {
    position: absolute; right: 35px; top: 136px;
    text-align: right; color: var(--white); font-family: var(--sans);
  }
  .holder__name { font-size: 28px; font-weight: 700; line-height: 36px; }
  .holder__role { font-size: 18px; font-weight: 400; line-height: 24px; margin-right: 8px; }

  .contacts {
    position: absolute; right: 28px; top: 300px;
    list-style: none; text-align: right;
    font-family: var(--sans); font-size: 17px; line-height: 24.5px;
    color: var(--white);
  }
  .contacts b { font-weight: 700; }

  .card--back .mark { left: 335px; top: 74px; width: 120px; height: 120px; }
  .card--back .brand-name {
    position: absolute; left: 0; right: 0; top: 250px;
    text-align: center;
    font-family: var(--serif); font-weight: 500; font-size: 46px;
    color: var(--navy); letter-spacing: 1px; line-height: 56px;
  }
  .rule {
    position: absolute; left: 131px; width: 526px; top: 311px;
    height: 2px; background: var(--navy);
  }
  .tagline {
    position: absolute; left: 0; right: 0; top: 322px;
    text-align: center;
    font-family: var(--serif); font-weight: 500; font-size: 20px;
    letter-spacing: 4px; color: var(--navy);
  }
  .web {
    position: absolute; left: 0; right: 0; top: 397px;
    text-align: center;
    font-family: var(--sans); font-size: 24px; color: var(--navy);
  }
</style>
</head>
<body>
<main class="canvas">

  <section class="card card--front" aria-label="Card front">
    <svg class="card__band" width="790" height="450" viewBox="0 0 790 450" aria-hidden="true">
      <path d="M583,0 C512,225 418,335 378,446" fill="none" stroke="var(--orange)" stroke-width="8"/>
      <path d="M598,0 L790,0 L790,450 L386,450 C428,335 525,230 598,0 Z" fill="var(--navy)"/>
    </svg>

    <div class="mark" aria-hidden="true"></div>
    <p class="brand-name">Vistalume Works</p>

    <div class="holder">
      <p class="holder__name">Your Name</p>
      <p class="holder__role">Administrator</p>
    </div>

    <ul class="contacts">
      <li><b>m</b> : 0417 539 662</li>
      <li><b>e</b> : sales@vistalumeworks.com.au</li>
      <li><b>w</b> : vistalumeworks.com.au</li>
      <li><b>t</b> : twitter.com/vistalumeworks</li>
      <li><b>f</b> : facebook.com/vistalumeworks</li>
    </ul>
  </section>

  <section class="card card--back" aria-label="Card back">
    <div class="mark" aria-hidden="true"></div>
    <p class="brand-name">VISTALUME WORKS</p>
    <div class="rule"></div>
    <p class="tagline">FINE ART PHOTOGRAPHY</p>
    <p class="web">www.vistalumeworks.com.au</p>
  </section>

</main>
</body>
</html>
```